Updated DJ business Card showing other businesses

DJ Talbo offers professional mobile dj services including DJ. MC. Karaoke.
Hushwave Disco (will attach logo)
I also offer a 360 Photo Booth.

Contact info:
(405) 555-0147
mark.fenstell@pelimail.com
Social Media @DJTalboOKC

```html
<!DOCTYPE html>
<html lang="en">
<head>
<meta charset="utf-8">
<title>DJ Talbo Business Card</title>
<link rel="stylesheet" href="https://fonts.googleapis.com/css2?family=Montserrat:wght@600;700;800;900&display=swap">
<style>
  :root{
    --bg:#d9d9d9;
    --purple:#8a1c87;
    --purple-deep:#5c1466;
    --magenta:#c23ad0;
    --teal:#3aa7c4;
    --yellow:#f3e61b;
    --white:#ffffff;
    --ink:#111111;
    --red:#d8243f;
  }
  *{box-sizing:border-box;margin:0;padding:0}
  html,body{width:1200px;height:913px;overflow:hidden;background:var(--bg)}
  body{position:relative;font-family:"Montserrat",sans-serif}
  .card{position:absolute;width:560px;height:320px;border-radius:4px;overflow:hidden;box-shadow:0 10px 24px rgba(0,0,0,.35)}
  .card--front{left:60px;top:110px}
  .card--back{left:580px;top:483px;background:var(--purple);display:flex;align-items:center;justify-content:center}
  .card__photo{position:absolute;inset:0;
    background:
      radial-gradient(ellipse at 15% 70%, rgba(90,200,220,.85), transparent 55%),
      radial-gradient(ellipse at 80% 20%, rgba(230,90,240,.9), transparent 60%),
      linear-gradient(135deg,var(--teal) 0%,var(--magenta) 45%,var(--purple-deep) 100%);}
  .card__content{position:absolute;inset:0;padding:26px 28px}
  .brand-name{font-weight:900;font-size:46px;line-height:1;color:var(--white);letter-spacing:1px}
  .tagline{margin-top:10px;font-weight:800;font-size:17px;color:var(--yellow)}
  .services{margin-top:10px;font-weight:800;font-size:30px;color:var(--white);letter-spacing:1px}
  .offer-pill{margin-top:14px;display:inline-block;background:var(--purple);color:var(--white);
    font-weight:700;font-size:19px;padding:9px 26px;border-radius:30px;letter-spacing:.5px}
  .contact{position:absolute;right:28px;bottom:24px;list-style:none;color:var(--white);font-weight:600;font-size:14px;line-height:1.55}
  .contact li{display:flex;align-items:center;gap:8px}
  .contact svg{width:15px;height:15px;flex:none}
  .sub-brand{position:absolute;left:28px;bottom:24px;display:flex;align-items:center;gap:8px;
    font-weight:800;font-size:18px;color:var(--white)}
  .sub-brand__dot{width:22px;height:22px;border-radius:50%;background:var(--white)}
  .back-brand{display:flex;align-items:center;gap:18px;font-weight:900;font-size:44px;color:var(--white);letter-spacing:1px}
  .back-brand__dot{width:60px;height:60px;border-radius:50%;background:var(--white)}
</style>
</head>
<body>
  <section class="card card--front">
    <div class="card__photo" role="img" aria-label="DJ mixing on decks under purple and teal stage lights"></div>
    <div class="card__content">
      <h1 class="brand-name">DJ Talbo</h1>
      <p class="tagline">offers professional Mobile Dj Services including</p>
      <p class="services">DJ. MC. Karaoke</p>
      <p class="offer-pill">I also offer a 360 Photo Booth.</p>
    </div>
    <div class="sub-brand"><span class="sub-brand__dot"></span>Hushwave Disco</div>
    <ul class="contact">
      <li><svg viewBox="0 0 24 24" fill="none" stroke="#fff" stroke-width="2"><circle cx="12" cy="12" r="11"/><path d="M8 6l2 3-1.5 1.5a8 8 0 0 0 5 5L15 14l3 2-1 2c-5 0-10-5-10-10z" fill="#fff" stroke="none"/></svg>(405) 555-0147</li>
      <li><svg viewBox="0 0 24 24" fill="none" stroke="#fff" stroke-width="2"><rect x="2" y="5" width="20" height="14" rx="1"/><path d="M2 6l10 7 10-7"/></svg>mark.fenstell@pelimail.com</li>
      <li>Social Media @DJTalboOKC</li>
    </ul>
  </section>

  <section class="card card--back">
    <div class="back-brand"><span class="back-brand__dot"></span>Hushwave Disco</div>
  </section>
</body>
</html>
```